loyalty card design needed

Inner city Coffee shop/cafe- we need a loyalty card that will stand out in wallets.
Ideally we are wanting up to 4 rows of 10 sign boxes.

needs a note on it to say tenth coffee is free.

Target Market(s)

business people

Industry/Entity Type

Cafe

Contact Information for Business Card

COPPERLEAF BREW
418 Wendell Street
HOBART TASMANIA 7000
phone 03 62958034
www.copperleafbrew.com.au

Logo Text

COPPERLEAF BREW

Logo styles of interest
Wordmark Logo
Requirements
Must have
• Ideally we are wanting up to 4 rows of 10 sign boxes.

needs a note on it to say tenth coffee is free

colours as suggested in file upload
Nice to have
• really stand out form the rest of cards in a customers wallet.

```html
<!DOCTYPE html>
<html lang="en">
<head>
<meta charset="utf-8">
<title>Copperleaf Brew Loyalty Card</title>
<link rel="stylesheet" href="https://fonts.googleapis.com/css2?family=Archivo+Black&family=Open+Sans:wght@400;600;700&family=Kaushan+Script&family=Oswald:wght@500;700&display=swap">
<style>
  :root {
    --lime: #d3df3f;
    --lime-dark: #b9c62c;
    --magenta: #d61e58;
    --cream: #f4f2d2;
    --ink: #1b1b1b;
    --backdrop: #e6e6e3;
  }
  * { margin: 0; padding: 0; box-sizing: border-box; }
  html, body { width: 1200px; height: 1025px; overflow: hidden; background: var(--backdrop); }
  .stage { position: relative; width: 1200px; height: 1025px; }

  .card {
    position: absolute; left: 200px; width: 800px; height: 460px;
    border-radius: 6px; overflow: hidden;
    box-shadow: 0 6px 18px rgba(0,0,0,.18);
  }

  /* Front */
  .card-front { top: 35px; background: var(--lime); }
  .loyalty-tab {
    position: absolute; left: 300px; top: 0; width: 200px; height: 92px;
    background: var(--magenta);
    display: flex; align-items: center; justify-content: center;
  }
  .loyalty-tab span {
    font-family: "Kaushan Script", cursive; color: var(--lime); font-size: 34px;
  }
  .front-name {
    position: absolute; left: 0; right: 0; top: 150px; text-align: center;
    font-family: "Archivo Black", sans-serif; font-size: 66px; color: var(--ink);
    letter-spacing: 1px; line-height: 1;
  }
  .front-rule {
    position: absolute; left: 100px; right: 100px; top: 222px; height: 6px; background: var(--magenta);
  }
  .front-tagline {
    position: absolute; left: 0; right: 0; top: 240px; text-align: center;
    font-family: "Open Sans", sans-serif; font-size: 28px; color: var(--ink); letter-spacing: 1px;
  }
  .front-tagline .dot { color: var(--magenta); padding: 0 6px; }
  .front-band {
    position: absolute; left: 0; right: 0; bottom: 0; height: 120px;
    background: var(--magenta);
    display: flex; align-items: flex-end; justify-content: flex-end; padding: 0 40px 26px 0;
  }
  .front-band span {
    font-family: "Open Sans", sans-serif; font-weight: 700; font-size: 26px; color: var(--lime);
  }

  /* Back */
  .card-back { top: 530px; background: var(--cream); }
  .side-strip {
    position: absolute; left: 0; top: 0; bottom: 0; width: 62px; background: var(--magenta);
  }
  .side-strip span {
    position: absolute; left: 50%; top: 50%;
    transform: translate(-50%, -50%) rotate(-90deg);
    white-space: nowrap;
    font-family: "Open Sans", sans-serif; font-weight: 700; font-size: 22px; color: var(--cream);
  }
  .contact {
    position: absolute; left: 90px; top: 22px;
    font-family: "Open Sans", sans-serif; font-size: 17px; color: var(--ink); line-height: 26px;
  }
  .contact-line { display: flex; align-items: center; gap: 8px; }
  .contact-line svg { width: 16px; height: 16px; fill: var(--magenta); }
  .back-name {
    position: absolute; left: 90px; top: 78px;
    font-family: "Archivo Black", sans-serif; font-size: 40px; color: var(--ink); line-height: 1;
    padding-bottom: 6px; border-bottom: 5px solid var(--magenta);
  }
  .free-ribbon {
    position: absolute; right: 40px; top: 0; width: 150px; height: 120px;
  }
  .free-ribbon svg { position: absolute; inset: 0; }
  .free-ribbon p {
    position: absolute; left: 0; right: 0; top: 14px; text-align: center;
    font-family: "Oswald", sans-serif; font-weight: 700; color: var(--cream);
    font-size: 26px; line-height: 30px;
  }
  .free-ribbon sup { font-size: 14px; }

  .stamp-grid {
    position: absolute; left: 90px; right: 30px; top: 150px; bottom: 20px;
    display: flex; flex-direction: column; justify-content: space-between;
  }
  .stamp-row {
    display: flex; align-items: center; gap: 12px; height: 66px;
    border-bottom: 3px dotted var(--magenta);
  }
  .stamp-row:last-child { border-bottom: none; }
  .stamp-box {
    width: 46px; height: 46px; background: var(--lime);
    border: 2px solid var(--lime-dark); transform: rotate(-8deg);
  }
  .free-cup { width: 62px; height: 54px; margin-left: 6px; }
</style>
</head>
<body>
<div class="stage">

  <section class="card card-front">
    <div class="loyalty-tab"><span>Loyalty Card</span></div>
    <h1 class="front-name">COPPERLEAF BREW</h1>
    <div class="front-rule"></div>
    <p class="front-tagline">Coffee<span class="dot">•</span>Food<span class="dot">•</span>Relax</p>
    <div class="front-band"><span>www.copperleafbrew.com.au</span></div>
  </section>

  <section class="card card-back">
    <div class="side-strip"><span>www.copperleafbrew.com.au</span></div>

    <div class="contact">
      <div class="contact-line">
        <svg viewBox="0 0 16 16"><path d="M3 1h3l1 4-2 1a9 9 0 0 0 5 5l1-2 4 1v3c0 1-1 2-2 2A13 13 0 0 1 1 3c0-1 1-2 2-2z"/></svg>
        <span>03 62958034</span>
      </div>
      <div class="contact-line">
        <svg viewBox="0 0 16 16"><path d="M8 1 1 7h2v8h4v-5h2v5h4V7h2z"/></svg>
        <span>418 Wendell Street HOBART TASMANIA 7000</span>
      </div>
    </div>

    <h2 class="back-name">COPPERLEAF BREW</h2>

    <div class="free-ribbon">
      <svg viewBox="0 0 150 120" preserveAspectRatio="none"><path d="M0 0H150V120L75 96 0 120Z" fill="var(--magenta)"/></svg>
      <p>10<sup>TH</sup> Coffee is<br>FREE</p>
    </div>

    <div class="stamp-grid">
      <div class="stamp-row">
        <div class="stamp-box"></div><div class="stamp-box"></div><div class="stamp-box"></div><div class="stamp-box"></div><div class="stamp-box"></div>
        <div class="stamp-box"></div><div class="stamp-box"></div><div class="stamp-box"></div><div class="stamp-box"></div><div class="stamp-box"></div>
        <svg class="free-cup" viewBox="0 0 62 54"><path d="M8 18h36v18a12 12 0 0 1-12 12H20A12 12 0 0 1 8 36z" fill="var(--ink)"/><path d="M44 22h6a6 6 0 0 1 0 12h-6" fill="none" stroke="var(--ink)" stroke-width="4"/><rect x="14" y="26" width="24" height="10" fill="var(--cream)"/><text x="26" y="34.5" font-family="Open Sans, sans-serif" font-size="8" font-weight="700" text-anchor="middle" fill="var(--ink)">FREE</text><path d="M20 4c-3 4 3 6 0 10M28 4c-3 4 3 6 0 10" fill="none" stroke="var(--ink)" stroke-width="2"/></svg>
      </div>
      <div class="stamp-row">
        <div class="stamp-box"></div><div class="stamp-box"></div><div class="stamp-box"></div><div class="stamp-box"></div><div class="stamp-box"></div>
        <div class="stamp-box"></div><div class="stamp-box"></div><div class="stamp-box"></div><div class="stamp-box"></div><div class="stamp-box"></div>
        <svg class="free-cup" viewBox="0 0 62 54"><path d="M8 18h36v18a12 12 0 0 1-12 12H20A12 12 0 0 1 8 36z" fill="var(--ink)"/><path d="M44 22h6a6 6 0 0 1 0 12h-6" fill="none" stroke="var(--ink)" stroke-width="4"/><rect x="14" y="26" width="24" height="10" fill="var(--cream)"/><text x="26" y="34.5" font-family="Open Sans, sans-serif" font-size="8" font-weight="700" text-anchor="middle" fill="var(--ink)">FREE</text><path d="M20 4c-3 4 3 6 0 10M28 4c-3 4 3 6 0 10" fill="none" stroke="var(--ink)" stroke-width="2"/></svg>
      </div>
      <div class="stamp-row">
        <div class="stamp-box"></div><div class="stamp-box"></div><div class="stamp-box"></div><div class="stamp-box"></div><div class="stamp-box"></div>
        <div class="stamp-box"></div><div class="stamp-box"></div><div class="stamp-box"></div><div class="stamp-box"></div><div class="stamp-box"></div>
        <svg class="free-cup" viewBox="0 0 62 54"><path d="M8 18h36v18a12 12 0 0 1-12 12H20A12 12 0 0 1 8 36z" fill="var(--ink)"/><path d="M44 22h6a6 6 0 0 1 0 12h-6" fill="none" stroke="var(--ink)" stroke-width="4"/><rect x="14" y="26" width="24" height="10" fill="var(--cream)"/><text x="26" y="34.5" font-family="Open Sans, sans-serif" font-size="8" font-weight="700" text-anchor="middle" fill="var(--ink)">FREE</text><path d="M20 4c-3 4 3 6 0 10M28 4c-3 4 3 6 0 10" fill="none" stroke="var(--ink)" stroke-width="2"/></svg>
      </div>
      <div class="stamp-row">
        <div class="stamp-box"></div><div class="stamp-box"></div><div class="stamp-box"></div><div class="stamp-box"></div><div class="stamp-box"></div>
        <div class="stamp-box"></div><div class="stamp-box"></div><div class="stamp-box"></div><div class="stamp-box"></div><div class="stamp-box"></div>
        <svg class="free-cup" viewBox="0 0 62 54"><path d="M8 18h36v18a12 12 0 0 1-12 12H20A12 12 0 0 1 8 36z" fill="var(--ink)"/><path d="M44 22h6a6 6 0 0 1 0 12h-6" fill="none" stroke="var(--ink)" stroke-width="4"/><rect x="14" y="26" width="24" height="10" fill="var(--cream)"/><text x="26" y="34.5" font-family="Open Sans, sans-serif" font-size="8" font-weight="700" text-anchor="middle" fill="var(--ink)">FREE</text><path d="M20 4c-3 4 3 6 0 10M28 4c-3 4 3 6 0 10" fill="none" stroke="var(--ink)" stroke-width="2"/></svg>
      </div>
    </div>
  </section>

</div>
</body>
</html>
```